Web design for financial services

A modern web design of financial services (brokerage firm)
Req.s and technology tags :
- Very mobile friendly.
- One paged with some inner pages.
- Animated sticky header .
- Member login area for e-trade.
- Support RTL language.
- HTML & CSS.

The logo will be Home link
• MPTR :
WHO WE ARE
Content :
i) Board of Directors
ii) Mission Statement
iii) Corporate Values
iv) Regulations
• Financial Services :
WHAT WE DO
Content:
i) Electronic trading
ii) Trading desk
iii) Institutional
iv) Investors Education
• News
• Market Tools
• Forms---- opens new page
• Careers---- opens new page
• Contact Us----opens new page

The website is :
http://www.mptr-doha-example.com/

The logo need some changes to be more modern and impressively , but with keeping same structure .

Some related websites :
https://www.lv-bourse.example/

financial market

Financial Service

Coded - Design and coding required

2 page

• same fonts of http://www.kwdholdings.example/

• - Very mobile friendly.
• - One paged with some inner pages.
• - Animated sticky header .
• - Member login area for e-trade.
• - Support RTL language.
• - HTML & CSS.
• Slider , some Qatari theme,
• i like the video inside the home page
• ex :http://www.kwdholdings.example/

```html
<!DOCTYPE html>
<html lang="en">
<head>
<meta charset="utf-8">
<title>MPTR – Financial Services</title>
<link rel="stylesheet" href="https://fonts.googleapis.com/css2?family=Roboto:wght@300;400;500;700&family=Lora:ital@1&display=swap">
<style>
:root{
  --red:#9b2421;
  --red-dark:#7f1b19;
  --ink:#333;
  --text:#666;
  --muted:#888;
  --line:#e4e4e4;
  --ring:#e6e6e6;
  --pale:#f4f5f7;
  --white:#fff;
  --star:#e8b400;
}
*{box-sizing:border-box;margin:0;padding:0}
html,body{width:1200px;height:2707px;overflow:hidden}
body{position:relative;background:var(--white);font-family:Roboto,Arial,sans-serif;color:var(--ink)}
.abs{position:absolute}

/* header */
.site-header{position:absolute;left:0;top:0;width:1200px;height:116px;background:var(--white)}
.top-rule{position:absolute;top:0;left:0;height:5px;width:816px;background:var(--red)}
.top-rule.grey{left:824px;width:376px;background:#999}
.brand{position:absolute;left:87px;top:40px;display:flex;align-items:center;gap:10px;font-weight:700;font-size:30px;color:var(--red)}
.brand .mark{width:18px;height:18px;background:var(--red)}
.login-btn{position:absolute;left:892px;top:22px;width:106px;height:36px;background:var(--red);border-radius:3px;color:#fff;font-size:15px;font-weight:500;display:flex;align-items:center;justify-content:center;gap:8px}
.lang{position:absolute;left:1005px;top:20px;width:109px;height:40px;border:1px solid #ccc;border-radius:3px;font-size:11px;display:flex;align-items:center;padding-left:10px;gap:6px}
.lang .flag{width:14px;height:9px;background:#2b3f8c}
.lang svg{margin-left:auto;margin-right:10px}
.main-nav{position:absolute;top:81px;left:0;font-size:13px;font-weight:500;color:#444}
.main-nav span{position:absolute;white-space:nowrap}
.main-nav .active{color:var(--red)}

/* hero */
.hero{position:absolute;top:116px;left:0;width:1200px;height:516px;background:linear-gradient(180deg,#4f8fcb 0%,#8fbde2 40%,#b9cedf 58%,#6e7682 72%,#3d4b5c 88%,#5a6f86 100%)}
.hero h1{position:absolute;top:84px;width:100%;text-align:center;color:#fff;font-size:52px;font-weight:500;letter-spacing:1px}
.hero p{position:absolute;top:158px;width:100%;text-align:center;color:#fff;font-size:20px;font-weight:300}

/* about rows */
.sec-title{position:absolute;font-size:21px;font-weight:500;color:#333;letter-spacing:.5px}
.sec-title::after{content:"";position:absolute;left:0;top:38px;width:63px;height:3px;background:var(--red)}
.body-copy{position:absolute;width:514px;font-size:12.5px;line-height:26px;color:var(--text);font-family:Arial,sans-serif}
.btn{position:absolute;background:var(--red);color:#fff;font-size:15px;font-weight:500;border-radius:3px;display:flex;align-items:center;justify-content:center}
.ring{position:absolute;border:9px solid var(--ring);border-radius:50%;display:flex;align-items:center;justify-content:center;background:#fff}
.divider{position:absolute;left:87px;top:989px;width:1028px;height:1px;background:var(--line)}

/* news */
.news{position:absolute;top:1337px;left:0;width:1200px;height:473px;background:var(--pale)}
.center-title{position:absolute;width:100%;text-align:center;font-size:22px;font-weight:500;color:#333}
.card{position:absolute;top:94px;width:328px}
.card .thumb{height:197px}
.card h3{margin-top:24px;font-size:13.5px;font-weight:700;color:#333}
.card p{margin-top:14px;font-size:12px;line-height:21px;color:var(--text);font-family:Arial,sans-serif}
.card .meta{margin-top:12px;font-family:Lora,serif;font-style:italic;font-size:12.5px;color:var(--red);display:flex;align-items:center;gap:6px}

/* testimonials */
.quote{position:absolute;top:1861px;width:340px}
.quote .avatar{position:absolute;left:0;top:0;width:86px;height:86px;border-radius:50%;background:linear-gradient(160deg,#c9a58a,#6f5647);border:3px solid #ddd}
.quote .words{position:absolute;left:108px;top:2px;width:255px;font-size:12px;line-height:21.5px;color:var(--text);font-family:Arial,sans-serif}
.quote .words b{font-family:Georgia,serif;font-size:20px;color:#aaa;margin-right:6px}
.quote .name{position:absolute;left:108px;top:113px;font-size:12px;font-weight:700;color:var(--red)}
.quote .date{position:absolute;left:108px;top:136px;font-size:12px;color:#444}
.quote .stars{position:absolute;left:108px;top:156px}
.slide-arrow{position:absolute;top:1908px}

/* market tools */
.tools{position:absolute;top:2081px;left:0;width:1200px;height:269px;background:var(--red)}
.tools .center-title{color:#fff;top:27px}
.tool{position:absolute;top:83px;width:240px;text-align:center}
.tool .disc{margin:0 auto;width:112px;height:112px;border-radius:50%;background:#fff;border:3px solid rgba(255,255,255,.4);outline:3px solid #fff;outline-offset:-9px;display:flex;align-items:center;justify-content:center}
.tool span{display:block;margin-top:21px;color:#fff;font-size:15px;font-weight:500}

/* footer */
.site-footer{position:absolute;top:2350px;left:0;width:1200px;height:357px;background:var(--pale)}
.footer-brand{position:absolute;left:112px;top:95px;display:flex;align-items:center;gap:14px;font-size:56px;font-weight:700;color:var(--red)}
.footer-brand .mark{width:28px;height:28px;background:var(--red)}
.f-title{position:absolute;top:73px;font-size:16px;font-weight:500;color:#333}
.contact-item{position:absolute;left:370px;font-size:11.5px;color:#555;display:flex;gap:12px;line-height:17px;font-family:Arial,sans-serif}
.contact-item svg{flex:none;margin-top:2px}
.f-copy{position:absolute;font-size:11.5px;line-height:19px;color:#555;font-family:Arial,sans-serif}
.email-field{position:absolute;left:635px;top:164px;width:212px;height:33px;border:1px solid #ddd;background:#fff;font-size:11.5px;color:#555;padding-left:14px;line-height:31px}
.subscribe{position:absolute;left:635px;top:213px;width:82px;height:27px;background:#888;color:#fff;font-size:10px;font-weight:500;display:flex;align-items:center;justify-content:center}
.social{position:absolute;top:191px;width:36px;height:36px;border:1.5px solid #bbb;border-radius:50%}
.f-rule{position:absolute;left:87px;top:283px;width:1028px;height:1px;background:var(--line)}
.copyright{position:absolute;top:313px;width:100%;text-align:center;font-size:12px;color:#666}
</style>
</head>
<body>

<header class="site-header">
  <div class="top-rule"></div><div class="top-rule grey"></div>
  <div class="brand"><span class="mark"></span>MPTR</div>
  <div class="login-btn">
    <svg width="12" height="14" viewBox="0 0 12 14"><rect x="1" y="6" width="10" height="8" fill="#fff"/><path d="M3 6V4a3 3 0 0 1 6 0v2" stroke="#fff" stroke-width="1.8" fill="none"/></svg>
    LOGIN
  </div>
  <div class="lang"><span class="flag"></span>English
    <svg width="10" height="6" viewBox="0 0 10 6"><path d="M1 1l4 4 4-4" stroke="#333" stroke-width="1.6" fill="none"/></svg>
  </div>
  <nav class="main-nav">
    <span class="active" style="left:476px">MPTR</span>
    <span style="left:556px">FINANCIAL SERVICE</span>
    <span style="left:731px">NEWS</span>
    <span style="left:819px">MARKET TOOL</span>
    <span style="left:960px">FORMS</span>
    <span style="left:1058px">CAREERS</span>
  </nav>
</header>

<section class="hero" role="img" aria-label="City skyline across the water under a blue sky">
  <h1>MPTR-QATAR</h1>
  <p>THOSE FACILITIES ENABLES CLIENTS TO TRADE FASTER, MORE SECURE &amp; PRIVATE.</p>
</section>

<section class="who-we-are">
  <h2 class="sec-title" style="left:184px;top:682px">WHO WE ARE</h2>
  <p class="body-copy" style="left:184px;top:741px">Meridian Premier Trading Resources is a private Qatari company that aims to provide secure and technologically advanced methods of trading to its clients. Those facilities enables clients to trade faster, more secure &amp; private. Having this strategy in our in minds, with this online portal we providing accurate, rapid and reliable order execution, attractive financial products and services, in line with compliance to regulatory rules and regulations.....</p>
  <div class="btn" style="left:184px;top:902px;width:137px;height:46px">ABOUT MPTR</div>
  <div class="ring" style="left:776px;top:677px;width:246px;height:246px">
    <svg width="90" height="110" viewBox="0 0 90 110" fill="none" stroke="#9b2421" stroke-width="2.5" stroke-linecap="round">
      <path d="M45 28c-14 0-24 10-24 23 0 9 5 14 9 19 3 4 4 7 4 11h22c0-4 1-7 4-11 4-5 9-10 9-19 0-13-10-23-24-23z"/>
      <path d="M34 88h22M35 95h20M39 102h12"/>
      <path d="M40 80V62l5-5 5 5v18"/>
      <path d="M45 4v12M23 10l5 10M67 10l-5 10M6 26l11 6M84 26l-11 6"/>
    </svg>
  </div>
</section>

<div class="divider"></div>

<section class="what-we-do">
  <div class="ring" style="left:186px;top:1023px;width:246px;height:246px">
    <svg width="126" height="110" viewBox="0 0 126 110" fill="none" stroke="#9b2421" stroke-width="2.5" stroke-linejoin="round">
      <rect x="4" y="4" width="118" height="78" rx="4"/>
      <rect x="13" y="13" width="100" height="60"/>
      <path d="M53 82l-4 20h28l-4-20M40 104h46"/>
      <circle cx="63" cy="43" r="7"/>
      <path d="M63 26v6M63 54v6M46 43h6M74 43h6M51 31l4 4M71 51l4 4M75 31l-4 4M55 51l-4 4"/>
      <circle cx="63" cy="43" r="13"/>
    </svg>
  </div>
  <h2 class="sec-title" style="left:511px;top:1027px">WHAT WE DO</h2>
  <p class="body-copy" style="left:511px;top:1084px">Meridian Premier Trading Resources is a private Qatari company that aims to provide secure and technologically advanced methods of trading to its clients. Those facilities enables clients to trade faster, more secure &amp; private. Having this strategy in our in minds, with this online portal we providing accurate, rapid and reliable order execution, attractive financial products and services, in line with compliance to regulatory rules and regulations.....</p>
  <div class="btn" style="left:511px;top:1245px;width:136px;height:47px">READ MORE</div>
</section>

<section class="news">
  <h2 class="center-title" style="top:35px">LATEST NEWS</h2>
  <article class="card" style="left:87px">
    <div class="thumb" role="img" aria-label="Aerial view of a coastal city with towers and turquoise water" style="background:linear-gradient(160deg,#c7a66e,#6c8fa0 55%,#2fa8c8)"></div>
    <h3>MERIDIAN PREMIER TRADING</h3>
    <p>Sed ut perspiciatis unde omnis iste natus error sit voluptatem accusantiumue ipsa beatae vitae dicta sunt explicabo.</p>
    <div class="meta"><svg width="12" height="12" viewBox="0 0 12 12" fill="none" stroke="#9b2421" stroke-width="1.3"><rect x="1" y="2" width="10" height="9"/><path d="M1 5h10M4 0v3M8 0v3"/></svg>1 month ago&nbsp;&nbsp;<svg width="13" height="12" viewBox="0 0 13 12" fill="none" stroke="#9b2421" stroke-width="1.3"><path d="M6.5 1C3.5 1 1 3 1 5.5c0 1.4.8 2.6 2 3.4L2.5 11l3-1.5c.3 0 .7.1 1 .1 3 0 5.5-2 5.5-4.5S9.5 1 6.5 1z"/></svg>05 Comments</div>
  </article>
  <article class="card" style="left:437px">
    <div class="thumb" role="img" aria-label="Glass towers by the waterfront under a grey sky" style="background:linear-gradient(180deg,#a9b3bd,#7e8b98 55%,#c3c9ce)"></div>
    <h3>MERIDIAN PREMIER TRADING</h3>
    <p>Sed ut perspiciatis unde omnis iste natus error sit voluptatem accusantiumue ipsa beatae vitae dicta sunt explicabo.</p>
    <div class="meta"><svg width="12" height="12" viewBox="0 0 12 12" fill="none" stroke="#9b2421" stroke-width="1.3"><rect x="1" y="2" width="10" height="9"/><path d="M1 5h10M4 0v3M8 0v3"/></svg>1 month ago&nbsp;&nbsp;<svg width="13" height="12" viewBox="0 0 13 12" fill="none" stroke="#9b2421" stroke-width="1.3"><path d="M6.5 1C3.5 1 1 3 1 5.5c0 1.4.8 2.6 2 3.4L2.5 11l3-1.5c.3 0 .7.1 1 .1 3 0 5.5-2 5.5-4.5S9.5 1 6.5 1z"/></svg>05 Comments</div>
  </article>
  <article class="card" style="left:787px">
    <div class="thumb" role="img" aria-label="Lit museum building and boat on the water at dusk" style="background:linear-gradient(180deg,#4d5a66,#6b6a66 50%,#a88a5c 70%,#2e2f33)"></div>
    <h3>MERIDIAN PREMIER TRADING</h3>
    <p>Sed ut perspiciatis unde omnis iste natus error sit voluptatem accusantiumue ipsa beatae vitae dicta sunt explicabo.</p>
    <div class="meta"><svg width="12" height="12" viewBox="0 0 12 12" fill="none" stroke="#9b2421" stroke-width="1.3"><rect x="1" y="2" width="10" height="9"/><path d="M1 5h10M4 0v3M8 0v3"/></svg>1 month ago&nbsp;&nbsp;<svg width="13" height="12" viewBox="0 0 13 12" fill="none" stroke="#9b2421" stroke-width="1.3"><path d="M6.5 1C3.5 1 1 3 1 5.5c0 1.4.8 2.6 2 3.4L2.5 11l3-1.5c.3 0 .7.1 1 .1 3 0 5.5-2 5.5-4.5S9.5 1 6.5 1z"/></svg>05 Comments</div>
  </article>
</section>

<section class="testimonials">
  <svg class="slide-arrow" style="left:44px" width="20" height="76" viewBox="0 0 20 76"><path d="M18 2L3 38l15 36" stroke="#ccc" stroke-width="1.5" fill="none"/></svg>
  <svg class="slide-arrow" style="left:1136px" width="20" height="76" viewBox="0 0 20 76"><path d="M2 2l15 36L2 74" stroke="#ccc" stroke-width="1.5" fill="none"/></svg>

  <div class="quote" style="left:87px">
    <div class="avatar" role="img" aria-label="Client portrait"></div>
    <p class="words"><b>“</b>Sed ut perspiciatis unde omnis iste natus error sit voluptatem accusantium doloremque laudantium, totam rem vitae dicta sunt explicabo.</p>
    <div class="name">JHON SMITH</div>
    <div class="date">POSTED ON 25 JUN 2017</div>
    <svg class="stars" width="48" height="9" viewBox="0 0 48 9" fill="none" stroke="#e8b400" stroke-width=".8"><g id="st"><path d="M4.5 .5l1.2 2.6 2.8.3-2.1 1.9.6 2.8-2.5-1.4-2.5 1.4.6-2.8L.5 3.4l2.8-.3z"/></g><use href="#st" x="10"/><use href="#st" x="20"/><use href="#st" x="30"/><use href="#st" x="40"/></svg>
  </div>
  <div class="quote" style="left:437px">
    <div class="avatar" role="img" aria-label="Client portrait"></div>
    <p class="words"><b>“</b>Sed ut perspiciatis unde omnis iste natus error sit voluptatem accusantium doloremque laudantium, totam rem vitae dicta sunt explicabo.</p>
    <div class="name">JHON SMITH</div>
    <div class="date">POSTED ON 25 JUN 2017</div>
    <svg class="stars" width="48" height="9" viewBox="0 0 48 9"><use href="#st"/><use href="#st" x="10"/><use href="#st" x="20"/><use href="#st" x="30"/><use href="#st" x="40"/></svg>
  </div>
  <div class="quote" style="left:787px">
    <div class="avatar" role="img" aria-label="Client portrait"></div>
    <p class="words"><b>“</b>Sed ut perspiciatis unde omnis iste natus error sit voluptatem accusantium doloremque laudantium, totam rem vitae dicta sunt explicabo.</p>
    <div class="name">JHON SMITH</div>
    <div class="date">POSTED ON 25 JUN 2017</div>
    <svg class="stars" width="48" height="9" viewBox="0 0 48 9"><use href="#st"/><use href="#st" x="10"/><use href="#st" x="20"/><use href="#st" x="30"/><use href="#st" x="40"/></svg>
  </div>
</section>

<section class="tools">
  <h2 class="center-title">MARKET TOOLS</h2>
  <div class="tool" style="left:131px">
    <div class="disc">
      <svg width="64" height="44" viewBox="0 0 64 44" fill="none" stroke="#9b2421" stroke-width="2.5" stroke-linejoin="round" stroke-linecap="round">
        <path d="M2 8l10-4 8 20-10 4zM62 8l-10-4-8 20 10 4z"/>
        <path d="M14 10c6 0 10-3 16-2l8 2M50 10c-5 1-9 0-14 3l-8 6c-2 2 0 5 3 4l7-4 10 10"/>
        <path d="M16 26l12 12c2 2 4 0 3-2M22 28l10 10c2 2 4 0 3-2M28 28l8 8c2 1 4-1 2-3"/>
      </svg>
    </div>
    <span>MOST ACTIVE COMPANY</span>
  </div>
  <div class="tool" style="left:479px">
    <div class="disc">
      <svg width="44" height="50" viewBox="0 0 44 50" fill="#9b2421"><circle cx="22" cy="13" r="11"/><path d="M2 50c0-14 8-22 20-22s20 8 20 22z"/></svg>
    </div>
    <span>TOP GAINER</span>
  </div>
  <div class="tool" style="left:833px">
    <div class="disc">
      <svg width="60" height="60" viewBox="0 0 60 60" fill="none" stroke="#9b2421" stroke-width="2.5" stroke-linejoin="round" stroke-linecap="round">
        <rect x="14" y="14" width="32" height="32" rx="3"/>
        <path d="M34 22h-6a3 3 0 0 0 0 8h4a3 3 0 0 1 0 8h-6M30 19v3M30 38v3"/>
        <path d="M40 4l10 8-10 8M50 12H38M20 56L10 48l10-8M10 48h12"/>
      </svg>
    </div>
    <span>TOP LOSE</span>
  </div>
</section>

<footer class="site-footer">
  <div class="footer-brand"><span class="mark"></span>MPTR</div>

  <h3 class="f-title" style="left:370px">CONTACT US</h3>
  <div class="contact-item" style="top:120px"><svg width="12" height="12" viewBox="0 0 12 12" fill="#666"><rect x="0" y="3" width="12" height="9" rx="1"/><rect x="2" y="0" width="8" height="4" rx="1"/></svg>+974 40001234 (Phone)</div>
  <div class="contact-item" style="top:149px"><svg width="12" height="12" viewBox="0 0 12 12" fill="#666"><rect x="2" y="0" width="8" height="4"/><rect x="0" y="4" width="12" height="6" rx="1"/><rect x="2" y="9" width="8" height="3"/></svg>+974 40005678 (Fax)</div>
  <div class="contact-item" style="top:180px"><svg width="12" height="10" viewBox="0 0 12 10" fill="#666"><rect width="12" height="10" rx="1"/><path d="M0 1l6 4 6-4" stroke="#fff" fill="none"/></svg><u>info@mptr-doha-example.com</u></div>
  <div class="contact-item" style="top:213px"><svg width="10" height="13" viewBox="0 0 10 13" fill="#666"><path d="M5 0a5 5 0 0 0-5 5c0 4 5 8 5 8s5-4 5-8a5 5 0 0 0-5-5zm0 7a2 2 0 1 1 0-4 2 2 0 0 1 0 4z"/></svg><span>First Floor, Al Noor Tower,West Bay<br>opposite Harbour Mall</span></div>

  <h3 class="f-title" style="left:635px">NEWSLETTER</h3>
  <p class="f-copy" style="left:635px;top:115px;width:220px">Register Your email address to get information ablout us</p>
  <div class="email-field">Email Address</div>
  <div class="subscribe">SUBSCRIBE</div>

  <h3 class="f-title" style="left:908px;top:75px">FOLLOW US</h3>
  <p class="f-copy" style="left:908px;top:116px;width:210px">Lorem ipsum dolor sit amet, conse ctetur adipiscing elit. Nulla in purus nibh. Donec ornare</p>
  <span class="social" style="left:906px"></span>
  <span class="social" style="left:948px"></span>
  <span class="social" style="left:990px"></span>
  <span class="social" style="left:1032px"></span>
  <span class="social" style="left:1074px"></span>

  <div class="f-rule"></div>
  <p class="copyright">© Copyright 2017 MPTR All Rights Reserved.</p>
</footer>

</body>
</html>
```